ULMIRA card Technical Architecture

Hello everyone ULMIRA: It is a consulting firm in Architecture and Construction. I require a card duplexing, sober, elegant, classic but not boring. Update 1: Use the following data for the card. Name: Gonzalo Pereda Mauricio Villalta Position: COO Twitter: @ulmiraAT Homepage: ulmira-example.com home address not include the participation of all thank you.

Target Market(s)

Construction companies, Architects and Consulting Engineers

Industry/Entity Type

Consulting

Contact Information for Business Card

Los campos que debe tener:
Nombre, Cargo, email, homepage y twitter

Font styles to use
Serif
Sans Serif
Other font styles liked:
• Me gustan playfair display, open sans y roboto, pero estoy sujeto a sus propuestas

Requirements
Must have
• Colors: Present combined proposals in white, red, gray and black Update 1: The two names must be clearly differentiated from the two surnames
Nice to have
• They are free to present their best proposals. I will bring them immediate feedback to the extent you can go see their designs. Complete data for card and logo files will give the winner the

```html
<!DOCTYPE html>
<html lang="es">
<head>
<meta charset="utf-8">
<title>ULMIRA — Tarjeta de presentación</title>
<link rel="stylesheet" href="https://fonts.googleapis.com/css2?family=Montserrat:wght@400;700&family=Open+Sans:wght@400&display=swap">
<style>
  :root {
    --stage: #e6e6e6;
    --card-black: #050505;
    --card-white: #ffffff;
    --brand-red: #c22a2a;
    --deep-red: #6e1010;
    --ink: #1c1c1c;
    --on-dark: #ffffff;
  }
  * { box-sizing: border-box; margin: 0; padding: 0; }
  html, body { width: 1200px; height: 900px; overflow: hidden; }
  body {
    background: var(--stage);
    position: relative;
    font-family: "Open Sans", Arial, sans-serif;
  }
  .card {
    position: absolute;
    width: 600px;
    height: 343px;
    border-radius: 22px;
    box-shadow: 0 10px 28px rgba(0,0,0,0.18);
    overflow: hidden;
  }

  /* Front side */
  .card--front {
    left: 80px; top: 90px;
    background: var(--card-black);
  }
  .front__name {
    position: absolute; left: 0; right: 0; top: 138px;
    text-align: center;
    font-family: "Montserrat", Arial, sans-serif;
    font-weight: 700;
    font-size: 40px;
    color: var(--brand-red);
    line-height: 1;
  }
  .front__handle {
    position: absolute; bottom: 52px; left: 0; right: 0;
    display: flex; align-items: center; justify-content: center; gap: 10px;
    color: var(--on-dark); font-size: 15px;
  }
  .front__dot { width: 10px; height: 10px; border-radius: 50%; background: var(--on-dark); }

  /* Back side */
  .card--back {
    left: 520px; top: 467px;
    background: var(--card-white);
  }
  .company {
    position: absolute; left: 48px; top: 138px;
    display: flex; align-items: center; gap: 12px;
  }
  .company__mark { width: 18px; height: 18px; background: var(--brand-red); flex: none; }
  .company__name {
    font-family: "Montserrat", Arial, sans-serif;
    font-weight: 700;
    font-size: 36px;
    color: var(--ink);
    line-height: 1;
  }

  .person {
    position: absolute; left: 330px; top: 84px;
  }
  .person__given, .person__family {
    font-family: "Montserrat", Arial, sans-serif;
    font-weight: 700; font-size: 20px;
    color: var(--deep-red);
    line-height: 1.15;
  }
  .person__role { font-size: 12.5px; color: var(--ink); margin-bottom: 6px; }
  .contact { list-style: none; margin-top: 8px; }
  .contact__item {
    display: flex; align-items: center; gap: 8px;
    font-size: 13px; color: var(--ink); line-height: 1.55;
  }
  .contact__icon { width: 10px; height: 10px; flex: none; }
</style>
</head>
<body>

  <section class="card card--front" aria-label="Anverso de la tarjeta">
    <div class="front__name">ULMIRA</div>
    <div class="front__handle"><span class="front__dot"></span>@ulmiraAT</div>
  </section>

  <section class="card card--back" aria-label="Reverso de la tarjeta">
    <div class="company">
      <span class="company__mark"></span>
      <span class="company__name">ULMIRA</span>
    </div>

    <div class="person">
      <p class="person__given">Mauricio Gonzalo</p>
      <p class="person__role">COO</p>
      <p class="person__family">Pereda Villalta</p>
      <p class="person__role">Director de Operaciones</p>
      <ul class="contact">
        <li class="contact__item">
          <svg class="contact__icon" viewBox="0 0 10 10" aria-hidden="true"><path d="M2 1 L3.6 1 L4.2 3 L3.2 3.8 Q4 5.8 6.2 6.8 L7 5.8 L9 6.4 L9 8 Q8.6 9 7.6 9 Q1 8 1 2 Q1 1 2 1 Z" fill="#c22a2a"/></svg>
          (+571) 999 999 9999
        </li>
        <li class="contact__item">
          <svg class="contact__icon" viewBox="0 0 10 10" aria-hidden="true"><rect x="0.8" y="2" width="8.4" height="6" rx="1" fill="none" stroke="#c22a2a" stroke-width="1.3"/><path d="M1 2.4 L5 5.4 L9 2.4" fill="none" stroke="#c22a2a" stroke-width="1.1"/></svg>
          info@ulmira-example.com
        </li>
        <li class="contact__item">
          <svg class="contact__icon" viewBox="0 0 10 10" aria-hidden="true"><circle cx="5" cy="5" r="4.2" fill="none" stroke="#c22a2a" stroke-width="1.1"/><ellipse cx="5" cy="5" rx="1.8" ry="4.2" fill="none" stroke="#c22a2a" stroke-width="0.9"/><path d="M0.8 5 H9.2" stroke="#c22a2a" stroke-width="0.9"/></svg>
          www.ulmira-example.com
        </li>
      </ul>
    </div>
  </section>

</body>
</html>
```